Need Business Card for our Real Estate Business with Sales Executive's Picture

PANTONE 484 C ( RED)

PANTONE 2766 C ( BLUE

Industry/Entity Type

Real Estate

Contact Information for Business Card

Name, Mobile, email, & picture of Person
Agency Phone, address, Web address

Requirements
Must have
• Our Logo Colours, Agent Picture,

```html
<!DOCTYPE html>
<html lang="en">
<head>
<meta charset="utf-8">
<title>Dunmore Realty – Business Card</title>
<link href="https://fonts.googleapis.com/css2?family=Cinzel:wght@500&family=Tinos&family=Roboto:wght@400&display=swap" rel="stylesheet">
<style>
  :root {
    --backdrop: #e6e6e6;
    --card: #f4f4f4;
    --navy: #0a1437;
    --burgundy: #620a12;
    --white: #ffffff;
    --grey-text: #5a5a5a;
    --photo-suit: #1f3477;
    --photo-light: #e9e9ec;
  }
  * { margin: 0; padding: 0; box-sizing: border-box; }
  html, body {
    width: 1200px; height: 960px; overflow: hidden;
    background: var(--backdrop);
  }
  .canvas { position: relative; width: 1200px; height: 960px; }
  .card {
    position: absolute; width: 600px; height: 343px;
    background: var(--card); overflow: hidden;
  }
  .card--front { left: 314px; top: 113px; }
  .card--back { left: 311px; top: 472px; }

  .brand {
    position: absolute; left: 0; right: 0; text-align: center;
    font-family: "Cinzel", serif; font-weight: 500; color: var(--navy);
    display: flex; justify-content: center; align-items: center; gap: 10px;
    white-space: nowrap; line-height: 1;
  }
  .brand__mark { width: 11px; height: 11px; background: var(--burgundy); flex: none; }
  .card--front .brand { top: 112px; font-size: 30px; letter-spacing: 1px; }

  .contact-band {
    position: absolute; left: 0; top: 187px; width: 100%; height: 121px;
    background: var(--navy); color: var(--white); text-align: center;
    font-family: "Tinos", serif;
  }
  .contact-band__name {
    font-family: "Cinzel", serif; font-weight: 500;
    font-size: 22px; margin-top: 14px; letter-spacing: 0.5px;
  }
  .contact-band__role {
    display: flex; justify-content: center; align-items: center; gap: 6px;
    font-family: "Cinzel", serif; font-size: 13px; letter-spacing: 1px;
  }
  .contact-band__role::before, .contact-band__role::after {
    content: ""; width: 52px; height: 1px; background: var(--white);
  }
  .contact-band__address { font-size: 14px; margin-top: 10px; }
  .contact-band__lines { font-size: 14px; margin-top: 3px; white-space: nowrap; }

  .web-band {
    position: absolute; left: 0; top: 311px; width: 100%; height: 32px;
    background: var(--burgundy); color: var(--white); text-align: center;
    font-family: "Tinos", serif; font-size: 13px; letter-spacing: 3px; line-height: 32px;
  }

  .agent-photo {
    position: absolute; left: 20px; top: 15px; width: 237px; height: 328px;
    background: linear-gradient(180deg, var(--photo-light) 0%, var(--photo-light) 30%, var(--photo-suit) 45%, var(--navy) 100%);
  }
  .card--back .brand { left: 300px; right: 10px; top: 252px; font-size: 26px; letter-spacing: 0.5px; }
  .back-web {
    position: absolute; left: 300px; right: 10px; top: 299px; text-align: center;
    font-family: "Roboto", sans-serif; font-size: 14px; letter-spacing: 3px;
    color: var(--grey-text); white-space: nowrap;
  }
</style>
</head>
<body>
<main class="canvas">
  <section class="card card--front">
    <div class="brand"><span class="brand__mark"></span>DUNMORE REALTY</div>
    <div class="contact-band">
      <p class="contact-band__name">DANIEL REYES</p>
      <p class="contact-band__role">CEO/FOUNDER</p>
      <p class="contact-band__address">1420 Birchwood Court, Juneau, Alaska 99801</p>
      <p class="contact-band__lines">Phone: 555 214 7830 Mobile: 555 309 6142 Email: daniel@dunmorerealty.com</p>
    </div>
    <div class="web-band">www.dunmorerealty.com</div>
  </section>

  <section class="card card--back">
    <div class="agent-photo" role="img" aria-label="Portrait photo of the sales executive in a navy suit and striped tie"></div>
    <div class="brand"><span class="brand__mark"></span>DUNMORE REALTY</div>
    <p class="back-web">www.dunmorerealty.com</p>
  </section>
</main>
</body>
</html>
```